QuillVane needs a dashboard page designed

Redesign the dashboard shown in the provided images.

There are two images:
- dashboard.png
- dashboard-expanded.png

NOTE: The vocabulary navigation on the left will be a very long list of words 100s, so keep that in mind when you're designing both the vocab navigation and the expanded vocab popup.

In the dashboard.png picture, there needs to be a progress chart showing the word progress like the following: review 1(show it as completed) -> review 2(show the user they are here) -> review 3(unvisited) -> review 4(unvisited)

The do-not-design-this-page.png image is for your reference only. It is not to be designed. Use it to understand the overall look and feel of the website to help you create the best dashboard page possible.
Updates

Need extra days to review

Industry/Entity Type

Education English learning

Number of Pages Required

1 page

Requirements
Must have
• The main navigation and main header cannot change between pages. See the do-not-design page for the main navigateion and header.
Should not have
• Do not add a person profile. We will not have images of our users. Keep the icons in the main navigation as they are.

```html
<!DOCTYPE html>
<html lang="en">
<head>
<meta charset="utf-8">
<title>QuillVane Dashboard</title>
<link href="https://fonts.googleapis.com/css2?family=Poppins:wght@400;500;600;700&display=swap" rel="stylesheet">
<style>
:root{
  --side:#2b1838;--side-text:#cbbfd6;--side-muted:#9d8fab;
  --ink:#1d1a24;--muted:#6d6875;--page:#f4f2f6;
  --purple:#5b3fa6;--coral:#e2674b;--blue:#2f8fc2;--amber:#e2a726;
  --chip:#ebebeb;--line:#e3e1e6;--close:#ef5a4c;
}
*{box-sizing:border-box;margin:0;padding:0}
html,body{width:1200px;height:844px;overflow:hidden}
body{font-family:'Poppins',sans-serif;background:var(--page);position:relative;color:var(--ink)}
.abs{position:absolute}
.sidebar{left:0;top:0;width:228px;height:844px;background:var(--side)}
.brand{left:30px;top:33px;font-size:20px;font-weight:600;color:#e8e0ef}
.brand-sq{left:184px;top:42px;width:11px;height:11px;border:1.5px solid #bfb3cc;border-radius:2px}
.nav-active{left:0;top:92px;width:196px;height:37px;background:#f2eef5;border-radius:0 19px 19px 0}
.nav-active span{position:absolute;left:32px;top:10px;font-size:12px;font-weight:600;color:var(--amber)}
.nav-active i{position:absolute;right:18px;top:12px;width:12px;height:12px;background:var(--amber);border-radius:2px}
.side-all{left:35px;top:145px;width:160px;font-size:12px;color:var(--side-text);border-bottom:1px solid #3d2b4c;padding-bottom:10px}
.side-h{left:35px;font-size:13px;font-weight:600;color:#e8e0ef}
.side-q{left:182px;width:14px;height:14px;border:1px solid #bfb3cc;border-radius:50%;font-size:9px;color:#bfb3cc;text-align:center;line-height:12px}
.side-sub{left:34px;font-size:10px;font-weight:600;color:#7fa35a}
.side-item{left:36px;font-size:11px;color:var(--side-muted)}
.side-link{left:34px;font-size:12px;font-weight:600;color:#e8e0ef}
.side-link b{display:inline-block;width:12px;height:13px;background:var(--amber);border-radius:3px;margin-right:10px;vertical-align:-2px}
.top-icon{top:30px;width:15px;height:15px;border:1.5px solid var(--ink);border-radius:50%}
.avatar{left:1131px;top:22px;width:32px;height:32px;border-radius:50%;background:var(--amber);color:#fff;font-weight:600;text-align:center;line-height:32px;font-size:16px}
.card{top:71px;width:221px;height:82px;border:1.5px solid;border-radius:8px;background:#fff}
.card .lbl{position:absolute;left:30px;top:17px;font-size:11px;color:var(--ink)}
.card .st{position:absolute;left:30px;top:34px;font-size:12px;font-weight:600}
.card .bar{position:absolute;left:30px;top:55px;width:118px;height:4px;border-radius:2px;background:#eee}
.card .bar i{display:block;height:4px;border-radius:2px}
.card .dot{position:absolute;right:20px;top:20px;width:42px;height:42px;border-radius:50%;background:#f1eff3}
.chart-panel{left:274px;top:194px;width:675px;height:440px;background:#fff;border-radius:8px}
.art{left:956px;top:194px;width:221px;height:137px;border-radius:8px;background:linear-gradient(135deg,#fde3c2,#f6c98a)}
.art p{position:absolute;left:0;right:0;top:90px;text-align:center;font-size:9px;font-weight:700;color:#3a2a18;line-height:12px}
.band{left:278px;width:560px;height:36px;font-size:11px;color:var(--muted);padding:10px 15px}
.axis{left:278px;top:625px;width:888px;height:1px;background:#c9c6cc}
.tick{top:658px;font-size:9px;color:var(--ink)}
.date-range{left:702px;top:683px;font-size:10px;font-weight:500}
.title{left:279px;top:706px;font-size:21px;font-weight:700}
.para{left:280px;top:740px;width:850px;font-size:11px;line-height:16px;color:#333}
.dim{left:0;top:0;width:1200px;height:844px;background:rgba(70,58,90,.42)}
.modal{left:266px;top:206px;width:687px;height:317px;background:#fff;border-radius:27px}
.select{position:absolute;left:35px;top:25px;width:243px;height:33px;border:1px solid #d6d4d9;border-radius:17px;font-size:10px;font-weight:500;padding:8px 16px}
.select svg{position:absolute;right:18px;top:12px}
.close{position:absolute;left:634px;top:37px;width:18px;height:18px;border-radius:50%;background:var(--close)}
.rule{position:absolute;left:35px;width:616px;height:1px;background:var(--line)}
.sec-h{position:absolute;left:35px;font-size:13px;font-weight:600}
.sec-h span{display:inline-block;width:10px;height:10px;border:1px solid #555;border-radius:50%;font-size:7px;text-align:center;line-height:8px;margin-left:10px;vertical-align:1px;font-weight:400}
.sec-sub{position:absolute;left:35px;font-size:8px;font-weight:600}
.chip{position:absolute;height:21px;background:var(--chip);border-radius:3px;font-size:8.5px;text-align:center;line-height:21px;color:var(--ink)}
</style>
</head>
<body>
<aside class="abs sidebar">
  <div class="abs brand">QuillVane</div>
  <div class="abs brand-sq"></div>
  <div class="abs nav-active"><span>QuillVane</span><i></i></div>
  <div class="abs side-all">All</div>
  <div class="abs side-h" style="top:191px">Short-Term Memory</div><div class="abs side-q" style="top:197px">?</div>
  <div class="abs side-sub" style="top:209px">GRAB</div>
  <div class="abs side-h" style="top:242px">Working Memory</div><div class="abs side-q" style="top:246px">?</div>
  <div class="abs side-item" style="top:267px">Cool Down</div>
  <div class="abs side-item" style="top:285px">Crav</div>
  <div class="abs side-item" style="top:303px">Go For</div>
  <div class="abs side-item" style="top:321px">Go-To</div>
  <div class="abs side-item" style="top:338px">In The Mood For</div>
  <div class="abs side-item" style="top:356px">Sip</div>
  <div class="abs side-item" style="top:374px">Soothing</div>
  <div class="abs side-item" style="top:392px">Stick With</div>
  <div class="abs side-item" style="top:409px">Throw In/Throw On</div>
  <div class="abs side-h" style="top:439px">Long-Term Memory</div><div class="abs side-q" style="top:444px">?</div>
  <div class="abs side-item" style="top:456px;color:var(--side-text)">Give ItA Try</div>
  <div class="abs side-link" style="top:502px"><b></b>Daily English</div>
  <div class="abs side-link" style="top:537px"><b></b>Business</div>
</aside>

<div class="abs top-icon" style="left:1052px"></div>
<div class="abs top-icon" style="left:1077px"></div>
<div class="abs top-icon" style="left:1101px"></div>
<div class="abs avatar">S</div>

<div class="abs card" style="left:274px;border-color:var(--purple)"><div class="lbl">REVIEW 1</div><div class="st" style="color:var(--purple)">Completed</div><div class="bar"><i style="width:100%;background:var(--purple)"></i></div><div class="dot"></div></div>
<div class="abs card" style="left:501px;border-color:var(--coral)"><div class="lbl">REVIEW 2</div><div class="st" style="color:var(--coral)">You are here</div><div class="bar"><i style="width:40%;background:var(--coral)"></i></div><div class="dot"></div></div>
<div class="abs card" style="left:728px;border-color:var(--blue)"><div class="lbl">REVIEW 3</div><div class="st" style="color:var(--blue)">Unvisited</div><div class="bar"></div><div class="dot"></div></div>
<div class="abs card" style="left:956px;border-color:var(--amber)"><div class="lbl">REVIEW 4</div><div class="st" style="color:var(--amber)">Unvisited</div><div class="bar"></div><div class="dot"></div></div>

<div class="abs chart-panel"></div>
<div class="abs art" role="img" aria-label="Illustration of a student reading a book with ideas around"><p>START VOCABULARY<br>REVIEW EXERCISE 3</p></div>

<div class="abs band" style="top:551px;background:#f9e3e6">Short-Term Memory</div>
<div class="abs band" style="top:588px;background:#e3eaf5">Forgotten Memory</div>
<svg class="abs" style="left:560px;top:520px" width="350" height="106">
  <rect x="36" y="47" width="7" height="58" fill="var(--side)"/>
  <rect x="139" y="0" width="7" height="105" fill="var(--side)"/>
  <path d="M44 51 Q95 52 136 102" fill="none" stroke="#444" stroke-width="1" stroke-dasharray="2 3"/>
  <path d="M318 0 Q340 50 343 100" fill="none" stroke="#444" stroke-width="1" stroke-dasharray="2 3"/>
</svg>
<div class="abs" style="left:578px;top:542px;font-size:9px;background:#eee;padding:2px 5px;border-radius:3px">21 May</div>
<div class="abs axis"></div>
<div class="abs tick" style="left:280px">18 May</div><div class="abs tick" style="left:336px">12:00</div>
<div class="abs tick" style="left:384px">19 May</div><div class="abs tick" style="left:440px">12:00</div>
<div class="abs tick" style="left:488px">20 May</div><div class="abs tick" style="left:545px">12:00</div>
<div class="abs tick" style="left:593px">21 May</div><div class="abs tick" style="left:649px">12:00</div>
<div class="abs tick" style="left:696px">22 May</div><div class="abs tick" style="left:753px">12:00</div>
<div class="abs tick" style="left:801px">23 May</div><div class="abs tick" style="left:858px">12:00</div>
<div class="abs tick" style="left:905px">24 May</div><div class="abs tick" style="left:962px">12:00</div>
<div class="abs tick" style="left:1010px">25 May</div><div class="abs tick" style="left:1067px">12:00</div>
<div class="abs tick" style="left:1114px">26 May</div>
<div class="abs date-range">DATE RANGE</div>
<h1 class="abs title">QuillVane Learning Analysis</h1>
<p class="abs para">Lorem ipsum <b>dolor</b> sit amet, consectetur adipiscing elit. Nam <b>rutrum commodo</b> enim id bibendum. Nunc dignissim risus <b>dolor</b>nec finibus dictum eu. Aliquam sit amet euismod metus, quis malesuada erat. Sed at felis quis nulla feugiat cursus at at <b>dolor</b>. Maecenas pretium alquet dapibus. Fusce et eleifend massa. Sed convallis ex mi, at lobortis ligula congue vel.</p>

<div class="abs dim"></div>

<section class="abs modal">
  <div class="select">ALL<svg width="8" height="5" viewBox="0 0 8 5"><path d="M1 1l3 3 3-3" fill="none" stroke="#333" stroke-width="1.2"/></svg></div>
  <div class="close"><svg width="18" height="18"><path d="M6 6l6 6M12 6l-6 6" stroke="#fff" stroke-width="1.6"/></svg></div>
  <div class="rule" style="top:77px"></div>
  <div class="sec-h" style="top:92px">Short-Term Memory<span>?</span></div>
  <div class="sec-sub" style="top:117px">GRAB</div>
  <div class="rule" style="top:143px"></div>
  <div class="sec-h" style="top:159px">Working Memory<span>?</span></div>
  <div class="chip" style="left:37px;top:185px;width:53px">Cool Down</div>
  <div class="chip" style="left:98px;top:185px;width:53px">Crav</div>
  <div class="chip" style="left:158px;top:185px;width:54px">Go For</div>
  <div class="chip" style="left:219px;top:185px;width:54px">Go-To</div>
  <div class="chip" style="left:279px;top:185px;width:79px">In The Mood For</div>
  <div class="chip" style="left:365px;top:185px;width:47px">Sip</div>
  <div class="chip" style="left:419px;top:185px;width:60px">Soothing</div>
  <div class="chip" style="left:486px;top:185px;width:59px">Stick With</div>
  <div class="chip" style="left:553px;top:185px;width:97px">Throw In/Throw On</div>
  <div class="rule" style="top:225px"></div>
  <div class="sec-h" style="top:240px">Long-Term Memory<span>?</span></div>
  <div class="chip" style="left:37px;top:267px;width:66px">Give ItA Try</div>
</section>
</body>
</html>
```